BUSINESS CARD - HALLORAN FIELD SERVICES

I would like to create a business card for my fertilizer spreading business. I would like to incorporate my existing logo and also a description of the services offered. The business card will be given to farmers so must be kept simple but effective. It will also be left in stores so much also be eye catching in order to stand out from other cards.

Target Market(s)

FARMERS

Requirements
Must have
• FRONT OF CARD = EXISTING LOGO + "CUSTOMISED SPREADING" below the logo

REAR Of CARD = SERVICES OFFERED AND CONTACT DETAILS

- Bulk fertilizer including Lime, Gypsum, Manure & Compost
- Granular fertilizer including Single Super, Urea, Gran-am, & Custom Blends
- Modern equipment - Autosteer & Variable Rate Capable
- Friendly & Reliable Service
- Contact Gus: 0417 552 308
Nice to have
• utilize same color scheme as existing logo

```html
<!DOCTYPE html>
<html lang="en">
<head>
<meta charset="utf-8">
<title>Halloran Field Services – Business Card</title>
<link href="https://fonts.googleapis.com/css2?family=Montserrat:wght@500;600;800&display=swap" rel="stylesheet">
<style>
  :root{
    --stage:#ecebe8;
    --card-dark:#2f2f30;
    --card-light:#f4f4f3;
    --ink:#3c3c3d;
    --mist:#c9c9c9;
    --orange:#e08a2c;
  }
  *{box-sizing:border-box;margin:0;padding:0}
  html,body{width:1200px;height:800px;overflow:hidden}
  body{
    background:var(--stage);
    font-family:"Montserrat",Arial,sans-serif;
    display:flex;align-items:center;justify-content:center;gap:32px;
  }
  .card{
    width:560px;height:320px;position:relative;
    box-shadow:0 10px 30px rgba(0,0,0,.18);
  }
  /* Rear */
  .card--rear{background:var(--card-dark);padding:34px 36px;color:var(--mist)}
  .contact{display:flex;align-items:center;gap:14px;margin-bottom:22px}
  .contact__icon{width:40px;height:40px;flex:none}
  .contact__label{font-size:10px;font-weight:600;letter-spacing:.08em;text-transform:uppercase}
  .contact__phone{font-size:19px;font-weight:600;color:var(--orange);letter-spacing:.04em}
  .services{list-style:none;display:flex;flex-direction:column;gap:13px}
  .service{position:relative;padding-left:14px;text-transform:uppercase;letter-spacing:.05em}
  .service::before{content:"";position:absolute;left:0;top:6px;width:4px;height:4px;border-radius:50%;background:var(--mist)}
  .service__title{font-size:12.5px;font-weight:600;color:var(--mist)}
  .service__detail{font-size:12.5px;font-weight:600;color:var(--orange);margin-top:2px}
  /* Front */
  .card--front{background:linear-gradient(135deg,#f7f7f6 0%,#e4e4e3 100%);
    display:flex;flex-direction:column;align-items:center;justify-content:center}
  .brand{display:flex;align-items:center;gap:16px}
  .brand__dot{width:64px;height:64px;border-radius:50%;background:var(--ink);flex:none}
  .brand__name{font-size:30px;font-weight:800;color:var(--ink);line-height:1.05;letter-spacing:-.01em}
  .brand__rule{width:330px;height:3px;background:var(--orange);margin:16px 0 22px}
  .tagline{font-size:26px;font-weight:600;color:var(--orange);letter-spacing:.07em;text-transform:uppercase}
  .tagline__bar{width:360px;height:6px;background:var(--orange);margin-top:14px;opacity:.85}
</style>
</head>
<body>
  <section class="card card--rear" aria-label="Card rear">
    <div class="contact">
      <svg class="contact__icon" viewBox="0 0 40 40" aria-hidden="true">
        <circle cx="20" cy="20" r="20" fill="#e08a2c"/>
        <path d="M14 11c1-1 2.5-1 3.2.3l1.6 3c.5 1 .2 2-.6 2.6l-1.2.9c.9 2.2 2.7 4 4.9 4.9l.9-1.2c.6-.8 1.7-1.1 2.6-.6l3 1.6c1.3.7 1.3 2.2.3 3.2l-1.5 1.5c-1.3 1.3-3.3 1.6-5 .8-4.5-2.1-8-5.6-10.1-10.1-.8-1.7-.5-3.7.8-5z" fill="#2f2f30"/>
      </svg>
      <div>
        <p class="contact__label">Contact Gus:</p>
        <p class="contact__phone">0417 552 308</p>
      </div>
    </div>
    <ul class="services">
      <li class="service">
        <p class="service__title">Bulk fertilizer including</p>
        <p class="service__detail">Lime, gypsum, manure &amp; compost</p>
      </li>
      <li class="service">
        <p class="service__title">Granular fertilizer including</p>
        <p class="service__detail">Single super, urea, gran-am, &amp; custom blends</p>
      </li>
      <li class="service">
        <p class="service__title">Modern equipment</p>
        <p class="service__detail">Autosteer &amp; variable rate capable</p>
      </li>
      <li class="service">
        <p class="service__title">Friendly &amp; reliable service</p>
      </li>
    </ul>
  </section>

  <section class="card card--front" aria-label="Card front">
    <div class="brand">
      <span class="brand__dot" aria-hidden="true"></span>
      <p class="brand__name">Halloran Field<br>Services</p>
    </div>
    <div class="brand__rule"></div>
    <p class="tagline">Customised Spreading</p>
    <div class="tagline__bar"></div>
  </section>
</body>
</html>
```